Home Remodeling company needs a business card design

we need a business card design for home remodeling company in hamilton county, indiana USA. we offers a wide range of construction services including whole house renovations, Design and Build Basements and Kitchen and Bathroom Remodeling . we would like to see designs for both site of business card that use the same color of the company logo and also including all information below :
1- Karim Feltous CEO / General Contractor
2- all company contacts Telephone numbers ( 1-888-DULOM-47 ) ( 317-555-0193) email address ( info@dulomhome.com) website ( www.dulomhome.com ) and social media logos (Facebook- twitter- google plus )
3- company logo
4- licensed . insured . bonded

```html
<!DOCTYPE html>
<html lang="en">
<head>
<meta charset="utf-8">
<title>Dulom Home Remodeling – Business Card</title>
<link rel="stylesheet" href="https://fonts.googleapis.com/css2?family=Lato:wght@400;700;900&display=swap">
<style>
  :root {
    --backdrop: #8e8e8e;
    --card-light: #ececee;
    --brand-red: #a92a33;
    --ink-dark: #2f3033;
    --ink-mid: #45464a;
    --rule-grey: #a9a9ad;
    --paper-white: #ececee;
  }
  * { box-sizing: border-box; margin: 0; padding: 0; }
  html, body {
    width: 1105px; height: 1200px; overflow: hidden;
    background: var(--backdrop);
    font-family: "Lato", sans-serif;
  }
  .canvas { position: relative; width: 1105px; height: 1200px; }
  .card {
    position: absolute; left: 180px; width: 746px; height: 427px;
  }
  .card-front { top: 119px; background: var(--card-light); }
  .card-back { top: 636px; background: var(--brand-red); }

  /* Front */
  .brand { position: absolute; left: 66px; top: 82px; display: flex; align-items: center; gap: 14px; }
  .brand-square { width: 16px; height: 16px; background: var(--brand-red); }
  .brand-name {
    font-weight: 900; font-size: 70px; letter-spacing: 4px; line-height: 1;
    color: var(--ink-dark);
  }
  .person { position: absolute; left: 66px; top: 203px; }
  .person-name { font-weight: 700; font-size: 26px; color: var(--ink-dark); letter-spacing: 0.5px; }
  .person-title { margin-top: 6px; font-weight: 400; font-size: 21px; color: var(--brand-red); }

  .contacts { position: absolute; left: 66px; top: 288px; display: flex; }
  .contact-col { display: flex; flex-direction: column; gap: 9px; }
  .contact-col.phones { padding-right: 16px; border-right: 1.5px solid var(--rule-grey); }
  .contact-col.online { padding-left: 20px; }
  .contact-line { display: flex; align-items: center; gap: 10px; font-size: 19px; color: var(--ink-mid); line-height: 20px; }
  .contact-icon { width: 18px; height: 18px; fill: var(--ink-dark); flex: none; }

  /* Back */
  .back-name {
    position: absolute; left: 0; right: 0; top: 150px; text-align: center;
    font-weight: 900; font-size: 60px; letter-spacing: 4px; color: var(--paper-white);
  }
  .credentials {
    position: absolute; left: 0; right: 0; top: 320px; text-align: center;
    font-size: 21px; letter-spacing: 0.5px; color: var(--paper-white);
  }
  .social-row { position: absolute; left: 266px; top: 360px; width: 214px; height: 28px; }
</style>
</head>
<body>
<div class="canvas">
  <section class="card card-front">
    <div class="brand">
      <span class="brand-square"></span>
      <span class="brand-name">DULOM</span>
    </div>

    <div class="person">
      <p class="person-name">Karim Feltous</p>
      <p class="person-title">CEO / General Contractor</p>
    </div>

    <div class="contacts">
      <div class="contact-col phones">
        <p class="contact-line">
          <svg class="contact-icon" viewBox="0 0 24 24" aria-hidden="true"><path d="M6.6 10.8c1.4 2.8 3.8 5.1 6.6 6.6l2.2-2.2c.3-.3.7-.4 1-.2 1.1.4 2.3.6 3.6.6.6 0 1 .4 1 1V20c0 .6-.4 1-1 1C10.6 21 3 13.4 3 4c0-.6.4-1 1-1h3.5c.6 0 1 .4 1 1 0 1.3.2 2.5.6 3.6.1.3 0 .7-.2 1z"/></svg>
          1-888-DULOM-47
        </p>
        <p class="contact-line">
          <svg class="contact-icon" viewBox="0 0 24 24" aria-hidden="true"><path d="M7 1h10a2 2 0 0 1 2 2v18a2 2 0 0 1-2 2H7a2 2 0 0 1-2-2V3a2 2 0 0 1 2-2zm0 3v14h10V4zm5 15.5a1.2 1.2 0 1 0 0 2.4 1.2 1.2 0 0 0 0-2.4z"/></svg>
          317-555-0193
        </p>
      </div>
      <div class="contact-col online">
        <p class="contact-line">
          <svg class="contact-icon" viewBox="0 0 24 24" aria-hidden="true"><path d="M2 5h20v14H2zm2 2v.5l8 5 8-5V7zm0 2.8V17h16V9.8l-8 5z"/></svg>
          info@dulomhome.com
        </p>
        <p class="contact-line">
          <svg class="contact-icon" viewBox="0 0 24 24" aria-hidden="true"><circle cx="12" cy="12" r="9.5" fill="none" stroke="currentColor" stroke-width="0"/><path d="M12 2a10 10 0 1 0 0 20 10 10 0 0 0 0-20zm-1 17.9A8 8 0 0 1 4.1 10L9 15v1a2 2 0 0 0 2 2zm6.9-2.5A2 2 0 0 0 16 16h-1v-3a1 1 0 0 0-1-1H8v-2h2a1 1 0 0 0 1-1V7h2a2 2 0 0 0 2-2v-.4a8 8 0 0 1 2.9 12.8z"/></svg>
          www.dulomhome.com
        </p>
      </div>
    </div>
  </section>

  <section class="card card-back">
    <p class="back-name">DULOM</p>
    <p class="credentials">LICENSED | INSURED | BONDED</p>
    <svg class="social-row" viewBox="0 0 214 28" aria-label="Social media links">
      <line x1="0" y1="14" x2="66" y2="14" stroke="#ececee" stroke-width="1" opacity="0.6"/>
      <line x1="148" y1="14" x2="214" y2="14" stroke="#ececee" stroke-width="1" opacity="0.6"/>
      <circle cx="79" cy="14" r="12" fill="#ececee"/>
      <circle cx="107" cy="14" r="12" fill="#ececee"/>
      <circle cx="135" cy="14" r="12" fill="#ececee"/>
    </svg>
  </section>
</div>
</body>
</html>
```